Stationery Design Project for Nimbora, Chicago

Nimbora, a street parking application which helps car drivers find a street parking spot by offering an ideal path along which to look for parking. This path is calculated by our algorithm based on data (e.g. historical data, baseball games schedule, etc.). Along this path the driver will find a spot and will also save 70% of the search time. Customer we target is reg. between 21 and 45 yo.

We envision something young, fresh, bright and original. Slightly abstract maybe. It should represent the idea and elements of finding street parking in the city, e.g. car(s), parking spot, people, city, etc. (just ideas!).

Logo is attached.

Requirement:
- Business Cards (2 Sided Full Color CMYK)
- Letterhead (1 Sided Full Color CMYK)
- Envelope (1 Sided Full Color CMYK)
- Sticker (1 Sided Full Color CMYK), round with a 2inch diameter.

Reason: We're starting to get more and more designs and need more time to look into all of them. Very exciting!! Thanks to everybody!

Hi all, we're in the process of selecting our favs. Though choices!!! Really good submissions. Will keep you posted and sorry for the delay.

Target Market(s)

Car drivers and owners between 21 and 45

Industry/Entity Type

Parking

Requirements
Must have
• Sticker should be round and include company URL nimbora.com and the new logo which we will attach soon.
Should not have
• Should not be too serious or boring.

```html
<!DOCTYPE html>
<html lang="en">
<head>
<meta charset="utf-8">
<title>Nimbora – Business Card</title>
<link rel="stylesheet" href="https://fonts.googleapis.com/css2?family=Open+Sans:wght@400;600;700&display=swap">
<style>
  :root {
    --page-bg: #dcdcdc;
    --card-light: #f4f4f4;
    --card-mid: #d6d6d6;
    --blue-deep: #27318f;
    --blue-bright: #1b78c4;
    --ink-dark: #1f1f1f;
    --ink-grey: #555555;
    --ink-soft: #5e5e5e;
    --mono-dark: #111111;
    --mono-mid: #5a5a5a;
  }
  * { margin: 0; padding: 0; box-sizing: border-box; }
  html, body { width: 954px; height: 1200px; overflow: hidden; }
  body {
    position: relative;
    background: var(--page-bg);
    font-family: "Open Sans", Arial, sans-serif;
    color: var(--ink-grey);
  }
  .card {
    position: absolute;
    left: 88px;
    width: 797px;
    height: 453px;
    border-radius: 28px;
    overflow: hidden;
    background: linear-gradient(90deg, var(--card-light) 0%, #ececec 55%, var(--card-mid) 100%);
    box-shadow: 0 4px 10px rgba(0,0,0,0.25);
  }
  .card--front { top: 100px; }
  .card--back { top: 643px; }
  .card__band { position: absolute; inset: 0; width: 797px; height: 453px; }
  .brand { position: absolute; display: flex; align-items: center; }
  .brand__dot {
    width: 154px; height: 154px; border-radius: 50%;
    background: radial-gradient(circle at 45% 40%, var(--blue-bright) 0%, var(--blue-deep) 100%);
  }
  .brand__name {
    margin-left: 26px;
    font-size: 84px;
    font-weight: 600;
    letter-spacing: 1px;
    color: var(--ink-dark);
    line-height: 1;
  }
  .card--front .brand { left: 188px; top: 78px; }
  .card--back .brand { left: 175px; top: 155px; }
  .person {
    position: absolute; right: 310px; top: 296px; text-align: right;
  }
  .person__name { font-size: 22px; font-weight: 700; color: var(--ink-grey); line-height: 1.2; }
  .person__role { font-size: 18px; color: var(--ink-soft); margin-top: 2px; }
  .divider {
    position: absolute; left: 518px; top: 270px; width: 1.5px; height: 100px; background: #666;
  }
  .contacts {
    position: absolute; left: 539px; top: 265px; list-style: none;
    font-size: 18px; line-height: 27px; color: var(--ink-soft);
  }
  .contacts b { font-weight: 700; color: var(--ink-grey); }
  .address { position: absolute; font-size: 18px; color: var(--ink-soft); }
  .card--front .address { right: 43px; top: 403px; }
  .card--back .address { left: 242px; top: 386px; }
</style>
</head>
<body>

<section class="card card--front">
  <svg class="card__band" viewBox="0 0 797 453" aria-hidden="true">
    <defs>
      <radialGradient id="blueBand" cx="0.35" cy="0.45" r="0.8">
        <stop offset="0" stop-color="#1d85cc"/>
        <stop offset="1" stop-color="#27318f"/>
      </radialGradient>
    </defs>
    <path d="M0 0 H298 C120 70 30 260 170 453 H0 Z" fill="url(#blueBand)"/>
    <path d="M200 0 H226 C120 90 68 220 98 345 C66 230 100 90 200 0 Z" fill="#ffffff"/>
    <path d="M262 0 H294 C140 85 62 230 118 400 C50 250 100 95 262 0 Z" fill="#1b78c4"/>
  </svg>
  <div class="brand">
    <span class="brand__dot"></span>
    <span class="brand__name">Nimbora</span>
  </div>
  <div class="person">
    <p class="person__name">Your Name</p>
    <p class="person__role">Designation</p>
  </div>
  <span class="divider"></span>
  <ul class="contacts">
    <li><b>p</b> : 123-456-7890</li>
    <li><b>c</b> : 123-456-7890</li>
    <li><b>e</b> : name@website.com</li>
    <li><b>w</b> : www.website.com</li>
  </ul>
  <p class="address">City Name, Street Name, State Name, Country Code</p>
</section>

<section class="card card--back">
  <svg class="card__band" viewBox="0 0 797 453" aria-hidden="true">
    <defs>
      <radialGradient id="greyBand" cx="0.5" cy="0.45" r="0.8">
        <stop offset="0" stop-color="#7a7a7a"/>
        <stop offset="0.5" stop-color="#4a4a4a"/>
        <stop offset="1" stop-color="#111111"/>
      </radialGradient>
    </defs>
    <path d="M0 0 H298 C120 70 30 260 170 453 H0 Z" fill="url(#greyBand)"/>
    <path d="M200 0 H226 C120 90 68 220 98 345 C66 230 100 90 200 0 Z" fill="#ffffff"/>
    <path d="M262 0 H294 C140 85 62 230 118 400 C50 250 100 95 262 0 Z" fill="#111111"/>
  </svg>
  <div class="brand">
    <span class="brand__dot"></span>
    <span class="brand__name">Nimbora</span>
  </div>
  <p class="address">City Name, Street Name, State Name, Country Code</p>
</section>

</body>
</html>
```